Chilli Jam Range. Label refresh.

We are expanding the Dunmore’s Pantry condiment family with a bold new Chilli Jam range. This collection celebrates vibrant, spicy flavours crafted for the gourmet market. The range includes five chilli jams and one crunchy chilli oil.
We are also refreshing the label design for this range. We want to retain key brand elements so that existing customers can still easily identify Dunmore’s Pantry products on the shelf.

Label Details
Jar Size: All products: 250ml tall glass jar 135mm tall x 60mm diameter.
Label Orientation: wraparound preferred but can be two set front/back.
Mandatory Inclusions:
Dunmore’s Pantry logo (retain existing or refreshed version)
Product name (see list below)
Net weight: 250ml
Barcode
Nutrition panel
Ingredients list
Country of Origin Statement.
Allergen Advisory.
Use/storage instructions (we’ll supply)
Business name and address

I would like one label that i can overprint BLACK (only) onto. As flavours can change through the season. Label should be able to represent all of the products listed below.
Range includes:
Classic Chilli Jam
Green Chilli Jam
Smoky Chipotle Chilli Jam
Pineapple Habanero Chilli Jam
Chilli Roasted Garlic Jam
Crunchy Chilli Oil

Target Market(s)

People who like chilli. Gourmet foodies. People buying gifts.

Industry/Entity Type

Gourmet food. Gift shops. Delicatessen

Colors
F0912C
F2A743
F7CA91
FBE8D2
FDF5EE
EE7325
F08F49
F5BC92
FAE3D3
FDF4ED
EB3D1F
EC4F4E
F09395
F8D3D4
FCEDEE

Requirements
Must have
• Create a label that we can overprint on. We over print in black ink only. One label for 6 chilli flavours.
Nice to have
• Brand recognition: Retain key identifiers from the existing Dunmore’s Pantry labels . Balancing traditional charm with a contemporary gourmet feel. Shelf impact: Use rich, vibrant colour palettes and bold typography to create standout in gourmet and gift settings.

```html
<!DOCTYPE html>
<html lang="en">
<head>
<meta charset="utf-8">
<title>Dunmore’s Pantry Chilli Jam Label</title>
<link rel="stylesheet" href="https://fonts.googleapis.com/css2?family=Federo&family=Righteous&display=swap">
<style>
  :root {
    --backdrop-light: #FDF5EE;
    --backdrop-warm: #F7CA91;
    --band-orange: #F2A743;
    --band-orange-deep: #F0912C;
    --label-cream: #FBF6EE;
    --label-cream-shade: #F1EADD;
    --rule-dark: #2B2620;
    --title-red: #D0211E;
    --ink: #1E1B18;
    --brand-gold: #A8812F;
    --chilli-red: #C81E1E;
    --flame-orange: #EE7325;
  }
  * { box-sizing: border-box; margin: 0; padding: 0; }
  html, body { width: 1200px; height: 853px; overflow: hidden; }
  body {
    background: linear-gradient(90deg, var(--backdrop-light) 0%, #FCE4C8 60%, #FBDDBE 100%);
    display: flex;
    align-items: center;
    justify-content: center;
  }
  .jar-label {
    position: relative;
    width: 300px;
    height: 500px;
    background: var(--label-cream);
    display: flex;
    flex-direction: column;
    box-shadow: 0 6px 22px rgba(120, 70, 20, 0.12);
  }
  .edge-band {
    height: 34px;
    background: linear-gradient(180deg, var(--band-orange) 0%, var(--band-orange-deep) 100%);
  }
  .edge-rule {
    height: 3px;
    background: var(--rule-dark);
  }
  .edge-rule.thin { height: 1px; margin-top: 2px; }
  .label-body {
    flex: 1;
    display: flex;
    flex-direction: column;
    align-items: center;
    background: linear-gradient(180deg, var(--label-cream) 0%, var(--label-cream-shade) 100%);
    padding: 14px 18px 14px;
  }
  .brand-block {
    display: flex;
    align-items: center;
    gap: 10px;
    margin-top: 4px;
  }
  .brand-square {
    width: 18px;
    height: 18px;
    background: var(--brand-gold);
  }
  .brand-name {
    font-family: "Federo", sans-serif;
    font-size: 22px;
    letter-spacing: 0.12em;
    text-transform: uppercase;
    color: var(--rule-dark);
    white-space: nowrap;
  }
  .chilli-art {
    width: 230px;
    height: 150px;
    margin-top: 26px;
    border-radius: 10px;
    background: linear-gradient(160deg, var(--band-orange) 0%, var(--flame-orange) 45%, var(--chilli-red) 100%);
  }
  .product-name {
    margin-top: 30px;
    font-family: "Righteous", sans-serif;
    font-size: 40px;
    color: var(--title-red);
    letter-spacing: 0.02em;
    line-height: 1;
  }
  .product-tagline {
    margin-top: 26px;
    font-family: "Federo", sans-serif;
    font-size: 20px;
    line-height: 1.3;
    color: var(--ink);
    text-align: center;
    text-transform: uppercase;
  }
</style>
</head>
<body>
  <main class="jar-label">
    <div class="edge-band"></div>
    <div class="edge-rule"></div>
    <div class="edge-rule thin"></div>
    <section class="label-body">
      <div class="brand-block">
        <span class="brand-square"></span>
        <span class="brand-name">Dunmore’s Pantry</span>
      </div>
      <div class="chilli-art" role="img" aria-label="Illustration of a red chilli pepper with a green stem, engulfed in orange flames"></div>
      <h1 class="product-name">CHILLI JAM</h1>
      <p class="product-tagline">A roaring blend of<br>chilli and exotic spices</p>
    </section>
    <div class="edge-rule thin"></div>
    <div class="edge-rule"></div>
    <div class="edge-band"></div>
  </main>
</body>
</html>
```